Website for legal expungement services with button to qualify/disqualify potential clients

Brightpath Record Renewal, LLC is a law firm focusing in legal expungement servcies (allowing people to erase criminal court records, police records, proseution files, etc). I want a more modern look which exudes confidence in the services. I am looking for a clean website that looks very polished. I want to keep the pages to a minimum, as I want the page not so much to answer questions, but to direct traffic to contact the law office. I would like the main focus point to be an button which would take a client through a series of questions to see if they would qualify for the services; this serves two purposes 1) to collect contact info for future marketing via email and 2) eliminate individuals who we are currently unable to help. A current theme that I have played around with are "Change so much, you'll need to reintroduce yourself" alongside a picture of a guys hand outstretched.
On the landing page, I would like a very brief and to the point explanation of what the service would be (i.e. "Leave your past in the past; expunge all your criminal records" ), followed by a list of benefits that it provides. (NB: included is a file "law post card-02" that includes the main benefits to expungement). Also included are two logo files for a more updated logo I currently use ("BRR Logo" and BRR Logo2") (NB: I'm open to revisions on this as well). Lastly, I've had two very minor 'ads' that I did ("postcard back" and "KVT Ad") that I like the idea of.

Target Market(s)

Middle/upper-middle class, mostly male, people with a criminal record or criminal accusation

Industry/Entity Type

Legal Services

Coding

Coded - Design and coding required

Requirements
Must have
• Button that attracts attention up front (possibly stand out coloring) to click to open up a series of questions to qualify/eliminate prospects, and simultaneously gather their info. Also, must be mobile friendly.

```html
<!DOCTYPE html>
<html lang="en">
<head>
<meta charset="utf-8">
<title>Brightpath Record Renewal</title>
<link href="https://fonts.googleapis.com/css2?family=Cormorant+Garamond:wght@600;700&family=Roboto:wght@400;500;700&display=swap" rel="stylesheet">
<style>
:root{
  --navy:#0f3466;
  --navy-deep:#24385a;
  --gold:#d3a32b;
  --ink:#161616;
  --muted:#6b6b6b;
  --footer:#0b0b0b;
  --line:#bdbdbd;
}
*{margin:0;padding:0;box-sizing:border-box}
html,body{width:1200px;height:3183px;overflow:hidden;background:#fff}
body{position:relative;font-family:'Roboto',sans-serif;color:var(--ink)}
.btn{position:absolute;display:flex;align-items:center;justify-content:center;gap:12px;color:#fff;font-weight:700;font-size:18px;text-decoration:none}
.btn svg{width:24px;height:24px}
.btn-gold{background:var(--gold)}
.btn-navy{background:var(--navy)}

.topbar{position:absolute;top:0;left:0;width:1200px;height:3px;background:var(--navy)}
.header{position:absolute;top:3px;left:0;width:1200px;height:124px;background:#fff}
.brand{position:absolute;left:111px;top:48px;display:flex;align-items:center;gap:16px}
.brand-square{width:22px;height:22px;background:var(--navy)}
.brand-name{color:var(--navy);font-family:'Cormorant Garamond',serif;font-weight:700;font-size:21px;line-height:22px;letter-spacing:1px}
.nav a{position:absolute;top:82px;font-size:16px;color:#333;text-decoration:none}

.hero{position:absolute;top:127px;left:0;width:1200px;height:658px;background:var(--navy-deep)}
.hero-photo{position:absolute;left:0;top:0;width:700px;height:658px;background:linear-gradient(90deg,#5b6472 0%,#47546b 40%,#34466a 75%,rgba(36,56,90,0) 100%)}
.hero h1{position:absolute;right:111px;top:90px;text-align:right;color:#fff;font-family:'Cormorant Garamond',serif;font-weight:700;font-size:66px;line-height:78px;letter-spacing:1px}

.section-title{position:absolute;left:0;width:1200px;text-align:center;font-family:'Cormorant Garamond',serif;font-weight:700;font-size:52px;letter-spacing:1px;color:var(--ink)}
.section-title .accent{color:var(--navy)}
.lead{position:absolute;left:200px;width:800px;text-align:center;color:var(--muted);font-size:15.5px;line-height:27px}
.card{position:absolute;top:1048px;width:467px;height:282px;background:#fff;box-shadow:0 2px 12px rgba(0,0,0,.09)}
.card-img{position:absolute;left:6px;top:6px;width:224px;height:270px}
.card h3{position:absolute;left:257px;top:30px;width:200px;font-family:'Cormorant Garamond',serif;font-weight:700;font-size:25px;line-height:32px}
.card p{position:absolute;left:257px;top:104px;width:195px;color:var(--muted);font-size:11.5px;line-height:23px}
.card .more{position:absolute;left:257px;top:232px;color:var(--gold);font-size:12.5px;font-weight:700;text-decoration:underline}

.cases{position:absolute;top:1539px;left:0;width:1200px;height:536px;background:linear-gradient(120deg,#c99a23 0%,#d6a836 55%,#cfa02c 100%)}
.cases-photo{position:absolute;left:112px;top:71px;width:508px;height:394px;background:linear-gradient(135deg,#cfcfcf 0%,#9ea3ab 45%,#6d7480 100%);box-shadow:0 4px 14px rgba(0,0,0,.15)}
.cases h2{position:absolute;left:683px;top:86px;color:#fff;font-family:'Cormorant Garamond',serif;font-weight:700;font-size:54px;line-height:62px;letter-spacing:1px}
.cases ul{position:absolute;left:683px;top:238px;list-style:none}
.cases li{display:flex;align-items:center;gap:16px;height:44.5px;color:#fff;font-size:16px}
.cases li svg{width:24px;height:24px}

.benefits{position:absolute;top:2075px;left:0;width:1200px;height:666px}
.benefits text{font-family:'Roboto',sans-serif}

.footer{position:absolute;top:2741px;left:0;width:1200px;height:442px;background:var(--footer);color:#fff}
.footer h4{position:absolute;font-family:'Cormorant Garamond',serif;font-weight:700;font-size:29px}
.footer h5{position:absolute;font-family:'Cormorant Garamond',serif;font-weight:700;font-size:22px}
.footer .small{position:absolute;font-size:12.5px}
.footer .link{position:absolute;font-size:14px}
.field{position:absolute;left:805px;width:279px;height:46px;border:1px solid #fff;border-radius:3px;font-size:10.5px;display:flex;align-items:center;padding-left:24px}
.rule{position:absolute;left:111px;top:314px;width:977px;height:1px;background:#444}
.social{position:absolute;top:383px;width:30px;height:30px;border-radius:50%}
</style>
</head>
<body>

<div class="topbar"></div>
<header class="header">
  <div class="brand">
    <div class="brand-square"></div>
    <div class="brand-name">BRIGHTPATH<br>RECORD RENEWAL</div>
  </div>
  <a class="btn btn-gold" style="left:921px;top:14px;width:167px;height:50px;font-size:17px" href="#">Get A Quote
    <svg viewBox="0 0 24 24"><circle cx="12" cy="12" r="11" fill="#fff"/><path d="M6 12h10M12 7l5 5-5 5" stroke="var(--gold)" stroke-width="2.4" fill="none"/></svg></a>
  <nav class="nav">
    <a style="left:492px" href="#">Home</a>
    <a style="left:593px" href="#">About Us</a>
    <a style="left:716px" href="#">Our Services</a>
    <a style="left:863px" href="#">Our Benefits</a>
    <a style="left:1009px" href="#">Contact Us</a>
  </nav>
</header>

<section class="hero">
  <div class="hero-photo" role="img" aria-label="Man in a navy suit reaching out his hand for a handshake"></div>
  <h1>CHANGE SO<br>MUCH, YOU'LL<br>NEED TO<br>REINTRODUCE<br>YOURSELF</h1>
  <a class="btn btn-gold" style="left:842px;top:505px;width:247px;height:55px" href="#">Book An Appointment
    <svg viewBox="0 0 24 24"><circle cx="12" cy="12" r="11" fill="#fff"/><path d="M6 12h10M12 7l5 5-5 5" stroke="var(--gold)" stroke-width="2.4" fill="none"/></svg></a>
</section>

<h2 class="section-title" style="top:868px"><span class="accent">OUR</span> SERVICES</h2>
<p class="lead" style="top:950px">Sed ut perspiciatis unde omnis iste natus error sit voluptatem accusantium doloremque laudantium, totam rem aperiam, eaque ipsa quae ab illo inventore veritatis et quasi architecto beatae vitae dicta</p>

<article class="card" style="left:105px">
  <div class="card-img" role="img" aria-label="Hands gripping prison cell bars" style="background:linear-gradient(90deg,#3b4252,#7a7f88 55%,#2e3340)"></div>
  <h3>Leave Your Past In The Past</h3>
  <p>Sed ut perspiciatis unde omnis iste natus error sit voluptatem accusantium doloremque laudantium, totam rem aperiam, eaque ipsa quae ab illo</p>
  <a class="more" href="#">Read More</a>
</article>
<article class="card" style="left:628px">
  <div class="card-img" role="img" aria-label="Lawyer signing documents beside scales of justice" style="background:linear-gradient(135deg,#e9ecef,#b8bec6 60%,#8f8a78)"></div>
  <h3>Expunge All Your Criminal Records</h3>
  <p>Sed ut perspiciatis unde omnis iste natus error sit voluptatem accusantium doloremque laudantium, totam rem aperiam, eaque ipsa quae ab illo</p>
  <a class="more" href="#">Read More</a>
</article>

<a class="btn btn-gold" style="left:523px;top:1374px;width:154px;height:56px" href="#">View More
  <svg viewBox="0 0 24 24"><circle cx="12" cy="12" r="11" fill="#fff"/><path d="M6 12h10M12 7l5 5-5 5" stroke="var(--gold)" stroke-width="2.4" fill="none"/></svg></a>

<section class="cases">
  <div class="cases-photo" role="img" aria-label="Young lawyer working on a laptop at a desk with scales of justice"></div>
  <h2>WHAT TYPES OF<br>CASES QUALIFY</h2>
  <ul>
    <li><svg viewBox="0 0 24 24"><circle cx="12" cy="12" r="11" fill="#fff"/><path d="M6 12h10M12 7l5 5-5 5" stroke="var(--gold)" stroke-width="2.4" fill="none"/></svg>Criminal accusations that were dismissed</li>
    <li><svg viewBox="0 0 24 24"><circle cx="12" cy="12" r="11" fill="#fff"/><path d="M6 12h10M12 7l5 5-5 5" stroke="var(--gold)" stroke-width="2.4" fill="none"/></svg>Criminal cases that went into a diversionary program</li>
    <li><svg viewBox="0 0 24 24"><circle cx="12" cy="12" r="11" fill="#fff"/><path d="M6 12h10M12 7l5 5-5 5" stroke="var(--gold)" stroke-width="2.4" fill="none"/></svg>Convictions</li>
  </ul>
  <a class="btn btn-navy" style="left:682px;top:389px;width:155px;height:55px" href="#">View More
    <svg viewBox="0 0 24 24"><circle cx="12" cy="12" r="11" fill="#fff"/><path d="M6 12h10M12 7l5 5-5 5" stroke="var(--navy)" stroke-width="2.4" fill="none"/></svg></a>
</section>

<section class="benefits" aria-label="Benefits to expunging">
  <svg width="1200" height="666" viewBox="0 0 1200 666">
    <defs>
      <filter id="sh" x="-10%" y="-20%" width="120%" height="140%"><feDropShadow dx="0" dy="2" stdDeviation="3" flood-opacity=".16"/></filter>
    </defs>
    <g stroke="var(--line)" stroke-width="3">
      <line x1="520" y1="153" x2="560" y2="228"/>
      <line x1="680" y1="153" x2="645" y2="228"/>
      <line x1="420" y1="258" x2="470" y2="290"/>
      <line x1="780" y1="258" x2="738" y2="290"/>
      <line x1="426" y1="398" x2="470" y2="380"/>
      <line x1="776" y1="398" x2="738" y2="380"/>
      <line x1="520" y1="505" x2="560" y2="440"/>
      <line x1="680" y1="505" x2="645" y2="440"/>
    </g>
    <circle cx="604" cy="332" r="146" fill="#ececec"/>
    <circle cx="604" cy="332" r="134" fill="#fff" filter="url(#sh)"/>
    <g font-weight="700" text-anchor="middle" font-size="32" style="font-family:'Cormorant Garamond',serif">
      <text x="604" y="305" fill="var(--navy)" letter-spacing="1" style="font-family:'Cormorant Garamond',serif">BENEFITS</text>
      <text x="604" y="348" fill="var(--navy)" style="font-family:'Cormorant Garamond',serif">TO</text>
      <text x="604" y="390" fill="#161616" letter-spacing="1" style="font-family:'Cormorant Garamond',serif">EXPUNGING</text>
    </g>

    <g filter="url(#sh)">
      <rect x="222" y="110" width="298" height="86" rx="43" fill="var(--gold)"/>
      <rect x="111" y="216" width="309" height="84" rx="42" fill="var(--navy)"/>
      <rect x="120" y="355" width="306" height="86" rx="43" fill="var(--gold)"/>
      <rect x="216" y="463" width="304" height="84" rx="42" fill="var(--navy)"/>
      <rect x="680" y="110" width="302" height="86" rx="43" fill="var(--navy)"/>
      <rect x="780" y="216" width="308" height="84" rx="42" fill="var(--gold)"/>
      <rect x="776" y="355" width="309" height="86" rx="43" fill="var(--navy)"/>
      <rect x="680" y="463" width="301" height="84" rx="42" fill="var(--gold)"/>
    </g>
    <g fill="#fff">
      <circle cx="265" cy="153" r="35"/><circle cx="153" cy="258" r="34"/>
      <circle cx="163" cy="398" r="35"/><circle cx="258" cy="505" r="34"/>
      <circle cx="939" cy="153" r="35"/><circle cx="1046" cy="258" r="34"/>
      <circle cx="1042" cy="398" r="35"/><circle cx="939" cy="505" r="34"/>
    </g>
    <g fill="none" stroke-width="4" stroke-linecap="round" stroke-linejoin="round">
      <path d="M253 154 L262 163 L278 145" stroke="var(--gold)"/>
      <path d="M141 259 L150 268 L166 250" stroke="var(--navy)"/>
      <path d="M151 399 L160 408 L176 390" stroke="var(--gold)"/>
      <path d="M246 506 L255 515 L271 497" stroke="var(--navy)"/>
      <path d="M927 154 L936 163 L952 145" stroke="var(--navy)"/>
      <path d="M1034 259 L1043 268 L1059 250" stroke="var(--gold)"/>
      <path d="M1030 399 L1039 408 L1055 390" stroke="var(--navy)"/>
      <path d="M927 506 L936 515 L952 497" stroke="var(--gold)"/>
    </g>

    <g font-size="11.5" fill="#fff">
      <text x="314" y="157">More options for housing</text>
      <text x="203" y="262">Protecting your privacy</text>
      <text x="211" y="402">Lower insurance premiums</text>
      <text x="307" y="499">Removing the stigma of having a</text>
      <text x="307" y="521">criminal record</text>
      <g text-anchor="end">
        <text x="889" y="143">More &amp; better job oppourtunities</text>
        <text x="889" y="165">leading to higher income</text>
        <text x="994" y="262">Better education opportunities</text>
        <text x="991" y="390">Qualifying for government</text>
        <text x="991" y="412">assistance programs</text>
        <text x="889" y="497">Loan qualification and better loan</text>
        <text x="889" y="519">rates</text>
      </g>
    </g>
  </svg>
</section>

<footer class="footer">
  <h4 style="left:115px;top:68px">Contact Us</h4>
  <h4 style="left:456px;top:68px">Quick Links</h4>
  <h4 style="left:801px;top:68px">Get In Touch</h4>

  <h5 style="left:117px;top:128px">Email Address</h5>
  <div class="small" style="left:117px;top:164px">info@brightpathrenewal.com</div>
  <h5 style="left:117px;top:211px">Contact Number</h5>
  <div class="small" style="left:117px;top:247px">555 014 2290</div>

  <div class="link" style="left:459px;top:128px">Home</div>
  <div class="link" style="left:459px;top:164px">Services</div>
  <div class="link" style="left:459px;top:200px">Benefits</div>
  <div class="link" style="left:459px;top:236px">Contact Us</div>
  <div class="link" style="left:576px;top:128px">About Us</div>
  <div class="link" style="left:576px;top:164px">Help</div>
  <div class="link" style="left:576px;top:200px">Privacy Policy</div>

  <div class="field" style="top:130px">Enter Your Name</div>
  <div class="field" style="top:189px">Enter Email Address
    <svg style="position:absolute;right:18px;top:13px" width="20" height="20" viewBox="0 0 20 20"><path d="M1 9 L19 1 L12 19 L9 11Z" fill="var(--gold)"/></svg>
  </div>

  <div class="rule"></div>
  <div class="small" style="left:0;width:1200px;text-align:center;top:346px;font-size:12px">© Copyright 2023 Brightpath Record Renewal | All Rights Reserved.</div>
  <div class="social" style="left:564px;background:#e1306c"></div>
  <div class="social" style="left:606px;background:#1877f2"></div>
</footer>

</body>
</html>
```